​Silver Harbor Rhythm provides personal, friendly service in a fun and high energy environment. We are based in Vermont.

We would like a card that appeals to a wide range of audiences as we do a wide range of events. Please feel free to check out our website silverharborrhythm.net for inspiration.

Target Market(s)

weddings, corporate, birthday parties, colleges

Industry/Entity Type

Business

Contact Information for Business Card

Silver Harbor Rhythm
Providing Entertainment For All Occasions
555 274 9160
silverharborrhythm@mailnest.net
silverharborrhythm.net

```html
<!DOCTYPE html>
<html lang="en">
<head>
<meta charset="utf-8">
<title>Silver Harbor Rhythm – Business Card</title>
<link rel="stylesheet" href="https://fonts.googleapis.com/css2?family=Open+Sans:wght@400;600;700&display=swap">
<style>
  :root {
    --page-bg: #e9e6e1;
    --card-white: #ffffff;
    --brand-green: #2f5e12;
    --brand-red: #b3262a;
    --card-black: #140407;
    --text-light: #ffffff;
    --text-soft: #e4ecdc;
    --shadow: rgba(0, 0, 0, 0.22);
  }
  * { box-sizing: border-box; margin: 0; padding: 0; }
  html, body {
    width: 1200px;
    height: 829px;
    overflow: hidden;
    background: var(--page-bg);
    font-family: "Open Sans", Arial, sans-serif;
  }
  .sheet {
    width: 1200px;
    height: 829px;
    display: flex;
    align-items: center;
    justify-content: center;
    gap: 50px;
  }
  .card {
    width: 525px;
    height: 300px;
    position: relative;
    box-shadow: 0 10px 24px var(--shadow);
    overflow: hidden;
  }

  /* Front */
  .card-front { display: flex; background: var(--card-white); }
  .front-brand {
    flex: 0 0 54%;
    display: flex;
    align-items: center;
    justify-content: center;
    gap: 10px;
    padding: 0 24px;
  }
  .brand-mark {
    width: 14px;
    height: 14px;
    background: var(--brand-red);
    flex: 0 0 auto;
  }
  .brand-name {
    font-size: 21px;
    font-weight: 700;
    color: var(--brand-green);
    letter-spacing: 0.5px;
    text-transform: uppercase;
    line-height: 1.15;
  }
  .front-contact {
    flex: 1;
    background: var(--brand-green);
    color: var(--text-light);
    padding: 26px 20px 0 24px;
    border-left: 3px solid #ffffff;
  }
  .person-name { font-size: 15px; font-weight: 700; }
  .person-title { font-size: 12px; color: var(--text-soft); margin-bottom: 22px; }
  .contact-list { list-style: none; font-size: 11px; color: var(--text-soft); }
  .contact-list li { display: flex; align-items: center; gap: 6px; margin-bottom: 4px; white-space: nowrap; }
  .contact-list svg { width: 10px; height: 10px; flex: 0 0 auto; }
  .address { margin-top: 24px; font-size: 11.5px; color: var(--text-soft); line-height: 1.7; }

  /* Back */
  .card-back {
    background: var(--card-black);
    display: flex;
    flex-direction: column;
    align-items: center;
    justify-content: center;
  }
  .back-brand {
    display: flex;
    align-items: center;
    gap: 14px;
    margin-top: -30px;
  }
  .back-brand .brand-mark { width: 20px; height: 20px; background: #ffffff; }
  .back-brand .brand-name { color: #ffffff; font-size: 30px; }
  .back-website {
    position: absolute;
    right: 34px;
    bottom: 34px;
    color: var(--text-light);
    font-size: 17px;
    letter-spacing: 1px;
  }
</style>
</head>
<body>
<main class="sheet">
  <section class="card card-front" aria-label="Card front">
    <div class="front-brand">
      <span class="brand-mark"></span>
      <span class="brand-name">Silver Harbor Rhythm</span>
    </div>
    <div class="front-contact">
      <p class="person-name">Your Name</p>
      <p class="person-title">Title</p>
      <ul class="contact-list">
        <li>
          <svg viewBox="0 0 10 10" aria-hidden="true"><path d="M2 1 L4 1 L4.6 3 L3.4 3.8 Q4.4 5.8 6.2 6.6 L7 5.4 L9 6 L9 8 Q5 9 2.5 6.5 Q1 4.5 2 1Z" fill="#fff"/></svg>
          555 274 9160
        </li>
        <li>
          <svg viewBox="0 0 10 10" aria-hidden="true"><rect x="0.5" y="2" width="9" height="6" fill="none" stroke="#fff"/><path d="M0.5 2 L5 5.5 L9.5 2" fill="none" stroke="#fff"/></svg>
          silverharborrhythm@mailnest.net
        </li>
        <li>
          <svg viewBox="0 0 10 10" aria-hidden="true"><circle cx="5" cy="5" r="4.3" fill="none" stroke="#fff"/><ellipse cx="5" cy="5" rx="1.8" ry="4.3" fill="none" stroke="#fff"/><path d="M0.7 5 H9.3" stroke="#fff"/></svg>
          www.silverharborrhythm.net
        </li>
      </ul>
      <p class="address">Sreet Name, City Name<br>Zip Code-00000</p>
    </div>
  </section>

  <section class="card card-back" aria-label="Card back">
    <div class="back-brand">
      <span class="brand-mark"></span>
      <span class="brand-name">Silver Harbor Rhythm</span>
    </div>
    <p class="back-website">www.silverharborrhythm.net</p>
  </section>
</main>
</body>
</html>
```